Powepoint Templates From Logo

We need 3 Powerpoint templates for use in a variety of presentations we develop and customize. Primary uses of the powerpoint presentations are for printed "pitch books" describing our firm's capabilities and approach (a lot of words with some design elements that we have developed), printed presentations of the results of financial evaluations of our clients (lots of charts and graphs) and as the talking points for speeches.

The design needs to be professional and "solid" to establish that we are capable of selling your multi-million dollar business, but also be a little different to show that we are not just boring MBA's.

Our current website and other materials have been developed internally and leave a great deal to be desired. I have initiated this project to demonstrate how much our look can be improved and, if successful, I hope to do much bigger projects in the future.
Updates

This is my first project and I thaank you all for your participation. Since I am new to this, I don;t know if I am providing the help and feedback as I should. Please feel free to let me know how I can be a better customer.

Target Market(s)

professionals (lawyers, accountaants), business owners, business groups, technology people

Industry/Entity Type

Financial

Requirements
Must have
• our logo
a place where logo of client can be inserted if appropriate
templates for the following pages
title page
standard bullet narrative page
page for charts and graphs to mostly fill the page
Should not have a lot of dark solid color that has to be printed.

Nice to have
• something to perk up the color a little

```html
<!DOCTYPE html>
<html lang="en">
<head>
<meta charset="utf-8">
<title>Bullet Narrative Page</title>
<link href="https://fonts.googleapis.com/css2?family=Oswald:wght@700&family=Arimo:wght@400;700&display=swap" rel="stylesheet">
<style>
  :root {
    --navy: #0d2f6b;
    --navy-rule: #1a3d73;
    --sky: #8fb3e0;
    --band-light: #dfe9f8;
    --white: #ffffff;
    --ink: #000000;
  }
  html, body {
    margin: 0;
    padding: 0;
    width: 1200px;
    height: 900px;
    overflow: hidden;
    background: var(--white);
  }
  .slide {
    position: relative;
    width: 1200px;
    height: 900px;
    background: var(--white);
    font-family: "Arimo", Arial, sans-serif;
    overflow: hidden;
  }
  .header-band {
    position: absolute;
    left: 0; top: 0;
    width: 1200px; height: 92px;
    background: linear-gradient(90deg, var(--band-light) 0%, #f3f7fd 55%, var(--white) 100%);
    border-bottom: 3px solid var(--navy-rule);
  }
  .project-title {
    position: absolute;
    right: 22px; top: 8px;
    margin: 0;
    font-family: "Oswald", "Arial Narrow", sans-serif;
    font-weight: 700;
    font-size: 58px;
    line-height: 1.2;
    color: var(--navy);
    letter-spacing: -0.5px;
  }
  .sub-heading {
    position: absolute;
    left: 78px; top: 182px;
    margin: 0;
    font-weight: 700;
    font-size: 41px;
    line-height: 1;
    color: var(--sky);
  }
  .bullet-list {
    position: absolute;
    left: 78px; top: 262px;
    margin: 0; padding: 0;
    list-style: none;
  }
  .bullet-list li {
    position: relative;
    height: 55.5px;
    padding-left: 29px;
    font-size: 23.5px;
    line-height: 30px;
    color: var(--ink);
  }
  .bullet-list li.bullet::before {
    content: "";
    position: absolute;
    left: 0; top: 10px;
    width: 9px; height: 9px;
    border-right: 3.5px solid var(--navy);
    border-top: 3.5px solid var(--navy);
    transform: rotate(45deg);
    transform-origin: center;
    margin-left: -4px;
  }
  .footer-band {
    position: absolute;
    left: 0; top: 780px;
    width: 1200px; height: 120px;
    border-top: 6px solid var(--navy-rule);
    background: linear-gradient(90deg, var(--band-light) 0%, #f3f7fd 55%, var(--white) 100%);
    box-sizing: border-box;
  }
  .page-number {
    position: absolute;
    left: 40px; top: 833px;
    font-size: 22px;
    color: var(--ink);
  }
  .firm-mark {
    position: absolute;
    right: 22px; top: 832px;
    display: flex;
    align-items: center;
    gap: 12px;
  }
  .firm-mark .mark-square {
    width: 30px; height: 30px;
    background: var(--navy);
  }
  .firm-mark .firm-name {
    font-weight: 700;
    font-size: 27px;
    color: var(--navy);
    letter-spacing: 0.5px;
  }
</style>
</head>
<body>
  <div class="slide">
    <header class="header-band">
      <h1 class="project-title">PROJECT TITLE HERE</h1>
    </header>

    <h2 class="sub-heading">SUB TEXT HERE</h2>

    <ul class="bullet-list">
      <li class="bullet">Lorem ipsum dolor sit ipsum, Lorem ipsum dolor sit ipsum</li>
      <li class="bullet">Lorem ipsum dolor sit ipsum, Lorem ipsum dolor sit ipsum</li>
      <li class="bullet">Lorem ipsum dolor sit ipsum Lorem ipsum dolor sit ipsum</li>
      <li class="bullet">Lorem ipsum dolor sit ipsum, Lorem ipsum dolor sit ipsum</li>
      <li class="continuation">Lorem ipsum dolor sit ipsum, Lorem ipsum dolor sit ipsum</li>
      <li class="bullet">Lorem ipsum dolor sit ipsum Lorem ipsum dolor sit ipsum</li>
    </ul>

    <footer class="footer-band"></footer>
    <div class="page-number">PAGE 2 OF 2</div>
    <div class="firm-mark">
      <span class="mark-square"></span>
      <span class="firm-name">KESTREL HARBOR</span>
    </div>
  </div>
</body>
</html>
```